Smart, Classy, Conservative looking Legal Letterhead

I need a letterhead that when you look at it it "says to you " this is a well established law firm with very smart lawyers, which will one day be appearing before the Supreme Court of the USA. All information about the Law firm should appear at the top of the page. please no information in the footer.

Industry/Entity Type

Legal

Requirements
Must have
• The name of the law firm, both addresses, phone number and fax,, The names of the attorneys, the website.
• Fields that get changed such as the date, VIA, Address of who the letter is going to,
• Re, Index,
• should have a clean neat look, sleek
Nice to have
• some color would be nice. A logo of some sort could be nice as well. Maybe a single S or interlocking M's For Merriton and Merriton.
Should not have
• not too modern looking.

```html
<!DOCTYPE html>
<html lang="en">
<head>
<meta charset="utf-8">
<title>Merriton &amp; Merriton, llp — Letterhead</title>
<link rel="stylesheet" href="https://fonts.googleapis.com/css2?family=Mulish:wght@400;600;700&display=swap">
<style>
  :root {
    --backdrop: #ebebeb;
    --paper: #ffffff;
    --brand: #5f7d90;
    --brand-light: #7f9aab;
    --ink: #3b3b3b;
    --ink-soft: #6b6b6b;
    --rule: #b9c6cf;
  }
  * { margin: 0; padding: 0; box-sizing: border-box; }
  html, body {
    width: 1200px; height: 1084px; overflow: hidden;
    background: var(--backdrop);
    font-family: "Mulish", Helvetica, Arial, sans-serif;
    color: var(--ink);
  }
  .letterhead {
    position: absolute; left: 198px; top: 22px;
    width: 804px; height: 1040px;
    background: var(--paper);
    box-shadow: 0 2px 10px rgba(0,0,0,0.08);
  }

  /* Firm identity column */
  .firm { position: absolute; left: 62px; top: 120px; width: 172px; }
  .firm-mark { display: block; margin: 0 0 10px 2px; }
  .firm-name { font-size: 14px; font-weight: 700; color: var(--brand); letter-spacing: 0.1px; }
  .firm-tagline { font-size: 11px; color: var(--brand-light); margin-top: 2px; padding-bottom: 8px; border-bottom: 1px solid var(--rule); }
  .attorneys { list-style: none; margin-top: 9px; padding-bottom: 8px; border-bottom: 1px solid var(--rule); }
  .attorneys li { font-size: 9.5px; color: var(--brand-light); letter-spacing: 0.3px; line-height: 1.55; text-transform: uppercase; }
  .attorneys .note { font-size: 7px; text-transform: none; letter-spacing: 0; line-height: 1.2; }

  .offices { margin-top: 10px; font-style: normal; font-size: 10px; line-height: 1.45; color: var(--brand-light); }
  .offices .office-label { text-transform: uppercase; letter-spacing: 0.3px; }
  .offices .gap { margin-top: 6px; }
  .offices .web { font-weight: 700; color: var(--brand); margin-top: 6px; font-size: 9.5px; }

  /* Letter column */
  .letter { position: absolute; left: 262px; top: 126px; width: 480px; font-size: 11px; line-height: 1.55; }
  .field-label { font-size: 10px; letter-spacing: 0.5px; color: var(--ink-soft); text-transform: uppercase; }
  .delivery { font-weight: 700; text-transform: uppercase; font-size: 10.5px; margin-top: 18px; letter-spacing: 0.2px; }
  .recipient { margin-top: 2px; letter-spacing: 0.5px; line-height: 1.35; }
  .reference { margin-top: 20px; line-height: 1.35; }
  .reference b { font-weight: 700; display: inline-block; width: 42px; }
  .body-copy p { margin-top: 18px; }
  .closing { margin-top: 22px; margin-left: 232px; line-height: 1.4; }
</style>
</head>
<body>
<main class="letterhead">

  <aside class="firm">
    <svg class="firm-mark" width="40" height="40" viewBox="0 0 40 40" aria-hidden="true">
      <circle cx="20" cy="20" r="18" fill="var(--brand)"/>
    </svg>
    <div class="firm-name">Merriton &amp; Merriton, llp</div>
    <div class="firm-tagline">Attorneys At Law</div>
    <ul class="attorneys">
      <li>Michael Merriton, Esq.</li>
      <li>Daniel A. Merriton, Esq.</li>
      <li>Elizabeth Hartwell, Esq.</li>
      <li>Peter T. Ashford, Esq.*</li>
      <li class="note">*Admitted in NY &amp; NJ</li>
    </ul>
    <address class="offices">
      <div>118 Warren Street</div>
      <div>New York, New York 10007</div>
      <div class="office-label gap">Westchester Office</div>
      <div>27 Orchard Lane</div>
      <div>Briarcliff, New York 10510</div>
      <div class="gap">Tel: 914-555-0142</div>
      <div>Fax: 914-555-0178</div>
      <div class="web">www.MerritonLawGroup.com</div>
    </address>
  </aside>

  <section class="letter">
    <div class="field-label">Date</div>
    <div class="delivery">Via Lorem Ipsum Dolor Sit Amet</div>
    <div class="recipient">
      XXXXXXXX XXXXXX<br>
      XXXXXXXXXXXXXXXXXX<br>
      XXXXXXXXXXXXXXXXXX<br>
      XXXXXXXX XXXXXXXX<br>
      XXXXXXXXXXXXXX
    </div>
    <div class="reference">
      <div><b>Re:</b>XXXXXXXXXXXXXXXXXXXXX</div>
      <div><b>Index:</b>XXXXXXXX</div>
    </div>
    <div class="body-copy">
      <p>Lorem ipsum dolor sit amet, consectetur adipiscing elit. Duis porttitor gravida orci eu varius. In euismod metus vel finibus eleifend. Quisque ex dui, condimentum in cursus eget, ullamcorper nec metus. Vestibulum vitae elementum leo. Suspendisse dictum consequat tempus. Vivamus vel est convallis metus lacinia suscipit sit amet ac tellus. Phasellus quis ligula sit amet libero commodo finibus. Aenean ac condimentum risus. Curabitur egestas nisl vitae hendrerit imperdiet.</p>
      <p>Vestibulum eget congue tortor. Nunc luctus euismod velit, eu aliquet eros. Maecenas suscipit hendrerit orci quis mollis. Aliquam aliquam, urna ac sagittis consequat, ante dolor tempus elit, eu hendrerit velit orci nec tellus. Sed quis placerat massa, a ullamcorper urna. Nullam sit ex id mi tincidunt euismod. Mauris sit amet nisl arcu. Vivamus eu fermentum ipsum.</p>
      <p>Maecenas nec mi ipsum. Fusce hendrerit nunc ut felis ultrices, at laoreet est sodales. Aenean convallis nisi luctus nunc vulputate, a vulputate dolor eleifend. Cras ornare tellus a convallis dapibus. Mauris at nisl blandit tellus porta dapibus. Cras tempor libero quis aliquam dignissim, sem diam hendrerit tellus, sit amet finibus tortor arcu id est. Suspendisse porttitor arcu sit amet ante auctor tincidunt. Duis eu porttitor metus.</p>
    </div>
    <div class="closing">
      Respectfully,<br>
      Daniel A. Merriton
    </div>
  </section>

</main>
</body>
</html>
```